TALMORK

The business want a professional looking business card. We have a scetch we will add but want the extra upgrade, and would like more suggestions for variations of our business cards.

```html
<!DOCTYPE html>
<html lang="en">
<head>
<meta charset="utf-8">
<title>TALMORK business card</title>
<link href="https://fonts.googleapis.com/css2?family=Montserrat:wght@400;700&display=swap" rel="stylesheet">
<style>
  :root {
    --bg: #2b2b2b;
    --gold-light: #f4efe6;
    --gold-mid: #c9a45c;
    --gold-deep: #7a5424;
    --gold-text: #9a7330;
    --brown: #7a4f17;
    --ink: #2a2a2a;
    --paper: #ffffff;
    --ghost: #f0f0f0;
  }
  * { margin: 0; padding: 0; box-sizing: border-box; }
  html, body { width: 1200px; height: 875px; overflow: hidden; background: var(--bg); }
  .stage {
    width: 1200px; height: 875px;
    display: flex; align-items: center; justify-content: center; gap: 50px;
  }
  .card {
    width: 540px; height: 310px; border-radius: 16px;
    position: relative; overflow: hidden;
  }
  .card--front {
    background: linear-gradient(100deg, var(--gold-light) 0%, #dcc39a 28%, var(--gold-mid) 58%, var(--gold-deep) 100%);
    display: flex; align-items: center; justify-content: center;
  }
  .brand-name {
    font-family: "Montserrat", sans-serif;
    font-weight: 700; line-height: 1; letter-spacing: 0.04em;
  }
  .card--front .brand-name { font-size: 40px; color: var(--gold-text); }

  .card--back { background: var(--paper); }
  .ghost-shape {
    position: absolute; right: -40px; top: 30px;
    width: 250px; height: 250px; border-radius: 50%;
    background: var(--ghost);
  }
  .card--back .brand-name {
    position: absolute; left: 40px; top: 50px; font-size: 32px; color: var(--brown);
  }
  .person {
    position: absolute; left: 58px; top: 126px;
    font-family: "Montserrat", sans-serif;
  }
  .person__marker {
    position: absolute; left: -58px; top: 14px; width: 26px; height: 26px; background: var(--brown);
  }
  .person__name { font-weight: 700; font-size: 22px; color: var(--brown); }
  .person__role { font-size: 14px; color: var(--ink); margin-top: 2px; }
  .contacts {
    position: absolute; left: 58px; top: 196px; list-style: none;
    font-family: "Montserrat", sans-serif; font-size: 14px; color: var(--ink);
  }
  .contacts li { display: flex; align-items: center; gap: 10px; height: 26px; }
  .contacts svg { width: 13px; height: 13px; fill: var(--brown); flex: none; }
</style>
</head>
<body>
<main class="stage">
  <section class="card card--front" aria-label="Card front">
    <div class="brand-name">TALMORK</div>
  </section>

  <section class="card card--back" aria-label="Card back">
    <div class="ghost-shape" role="img" aria-label="Faint brand decoration"></div>
    <div class="brand-name">TALMORK</div>
    <div class="person">
      <span class="person__marker"></span>
      <div class="person__name">Lars Henrik Solvang</div>
      <div class="person__role">CEO &amp; Founder</div>
    </div>
    <ul class="contacts">
      <li>
        <svg viewBox="0 0 24 24" aria-hidden="true"><path d="M6.6 10.8a15 15 0 0 0 6.6 6.6l2.2-2.2a1 1 0 0 1 1-.25 11.4 11.4 0 0 0 3.6.57 1 1 0 0 1 1 1V20a1 1 0 0 1-1 1A17 17 0 0 1 3 4a1 1 0 0 1 1-1h3.5a1 1 0 0 1 1 1c0 1.25.2 2.45.57 3.57a1 1 0 0 1-.25 1z"/></svg>
        004791234567
      </li>
      <li>
        <svg viewBox="0 0 24 24" aria-hidden="true"><path d="M2 5h20v14H2zm2 2v.5l8 5 8-5V7l-8 5z"/></svg>
        contact@talmork.llc
      </li>
      <li>
        <svg viewBox="0 0 24 24" aria-hidden="true"><path d="M12 2a10 10 0 1 0 0 20 10 10 0 0 0 0-20zm0 2a8 8 0 0 1 7.7 6h-4.1a14 14 0 0 0-1.6-5.7A8 8 0 0 1 12 4zm-2 .3A14 14 0 0 0 8.4 10H4.3A8 8 0 0 1 10 4.3zM4.3 14h4.1a14 14 0 0 0 1.6 5.7A8 8 0 0 1 4.3 14zm5.7-4h4a12 12 0 0 1 0 4h-4a12 12 0 0 1 0-4zm4 9.7a14 14 0 0 0 1.6-5.7h4.1a8 8 0 0 1-5.7 5.7z"/></svg>
        www.talmork.llc
      </li>
    </ul>
  </section>
</main>
</body>
</html>
```